A weight loss and fitness website design

I am into different types of modern weight loss techniques for people who are a little fatty and wish to be physically and mentally fit. Basically, the website is to teach people how to reduce weight using different methods such as diet, exercises, yoga and other forms. I would need an eye catching website which would make visitors want to come back. The will be also be different forms of exercises for a health and fit life. This said, my website is to have two categories of
1) weight loss techniques
2) exercise of fit and healthy living.
I prefer bright colors such as green, blue, yellow, and orange. Imagery should include before and after pictures of people suffering from obesity, people under going exercises.
Designers can get ideas and inspiration from the website fitlumen.com which i was previously part of the team.
Target Market(s)
My target audience are people suffering from obesity, malnutrition and physical deficiency.
Industry/Entity Type
Fitness
Coding
Coded - Design and coding required
Number of Pages Required
1 page
Look and feel

```html
<!DOCTYPE html>
<html lang="en">
<head>
<meta charset="utf-8">
<title>Trimvale Fitness</title>
<link href="https://fonts.googleapis.com/css2?family=Jost:wght@400;500&family=Open+Sans:wght@400;600;700&display=swap" rel="stylesheet">
<style>
:root{
  --orange:#e8681c;
  --orange-dark:#d3520c;
  --green:#4f8c24;
  --green-dark:#3b6d17;
  --ink:#2b2b2b;
  --text:#555;
  --muted:#777;
  --dark:#1b1b1b;
  --light:#f4f4f4;
  --band:#e6e6e6;
  --white:#fff;
}
*{margin:0;padding:0;box-sizing:border-box}
html,body{width:1200px;height:3169px;overflow:hidden}
body{position:relative;background:var(--white);font-family:"Open Sans",Arial,sans-serif;color:var(--text)}
.abs{position:absolute}
.heading{font-family:"Jost","Futura",sans-serif;font-weight:400;text-transform:uppercase;text-align:center;color:var(--ink);font-size:36px;letter-spacing:.5px;white-space:nowrap}
.heading .accent{color:var(--orange)}
.ornament{position:absolute;height:2px;background:#333}
.ornament i{position:absolute;left:50%;top:-7px;width:14px;height:14px;margin-left:-7px;border-radius:50%;background:var(--orange);box-shadow:0 0 0 5px var(--white)}
.btn-green{display:flex;align-items:center;justify-content:center;background:linear-gradient(#5b9c2b,var(--green-dark));color:#fff;font-weight:700;font-size:12px;text-transform:uppercase;border-radius:2px}

/* hero */
.hero{left:0;top:0;width:1200px;height:655px;background:radial-gradient(ellipse at 55% 50%,#6a5a4c 0%,#3a342f 45%,#151515 100%)}
.brand{left:70px;top:25px;width:190px;text-align:center;color:#fff;font-family:"Jost",sans-serif;font-size:19px;font-weight:400;white-space:nowrap}
.brand .mark{display:block;width:46px;height:46px;margin:0 auto 8px;border-radius:50%;background:var(--orange)}
.nav{top:64px;font-weight:700;font-size:13px;color:#fff;text-transform:uppercase}
.nav span{position:absolute;white-space:nowrap}
.nav-underline{left:574px;top:88px}
.hero-title{left:0;top:305px;width:1200px;text-align:center;color:#fff;font-family:"Jost",sans-serif;font-weight:400;font-size:37px;letter-spacing:.5px}
.hero-sub{left:0;top:358px;width:1200px;text-align:center;color:#eee;font-family:"Jost",sans-serif;font-size:21px;letter-spacing:3px}
.hero-btn{left:471px;top:420px;width:258px;height:38px;border:1.5px solid rgba(255,255,255,.85);border-radius:19px;color:#fff;font-size:13px;letter-spacing:2px;display:flex;align-items:center;justify-content:center}
.scroll-down{left:562px;top:549px}
.arrow-side{top:296px}

/* welcome */
.intro{left:140px;top:775px;width:920px;text-align:center;font-size:12.5px;line-height:28px}
.feature{top:872px;width:250px;text-align:center}
.feature .circle{width:114px;height:114px;border-radius:50%;margin:0 auto;background:var(--orange);display:flex;align-items:center;justify-content:center}
.feature .circle.active{background:var(--green);box-shadow:0 0 0 4px #fff,0 0 0 6px var(--green)}
.feature h3{font-family:"Jost",sans-serif;font-weight:400;font-size:19px;color:var(--ink);margin-top:14px}
.feature p{font-size:12.5px;line-height:22px;margin:6px 10px 0}

/* techniques */
.techniques{left:0;top:1152px;width:1200px;height:570px;background:linear-gradient(#262626,#3a3530 50%,#1a1a1a)}
.tech-sub{left:0;top:1266px;width:1200px;text-align:center;color:#fff;font-size:12.5px}
.tech-card{top:1310px;width:232px;height:353px;background:#fff;border:3px solid #fff;text-align:center}
.tech-card .photo{height:170px}
.tech-card h4{margin-top:30px;font-size:12.5px;font-weight:700;color:#222;text-transform:uppercase}
.tech-card p{font-size:12.5px;line-height:20px;margin-top:6px;color:var(--text)}
.tech-card .btn-green{width:108px;height:38px;margin:14px auto 0}

/* exercise */
.exercise-photo{left:99px;top:1777px;width:423px;height:256px;background:linear-gradient(110deg,#6b5145,#2c2a2b 55%,#4a4a4a);border:3px solid #e5e5e5}
.exercise-title{left:545px;top:1772px;width:537px;text-align:left;font-size:31px;letter-spacing:0}
.exercise-text{left:545px;top:1845px;width:543px;font-size:12.5px;line-height:23.6px;text-align:justify}
.exercise-btn{left:545px;top:1998px;width:100px;height:36px}

/* before after */
.results{left:0;top:2130px;width:1200px;height:596px;background:var(--light)}
.result-card{top:2255px;width:309px;height:416px;background:#fff;border:1px solid #ddd;text-align:center}
.result-card .photo{position:relative;height:207px;margin:4px;display:flex}
.result-card .photo div{flex:1}
.result-card .label{position:absolute;left:0;right:0;bottom:0;height:27px;background:rgba(110,110,110,.75);display:flex;color:#fff;font-size:14px}
.result-card .label span{flex:1;line-height:27px}
.result-card h4{margin-top:20px;font-family:"Jost",sans-serif;font-weight:400;font-size:23px;color:#222}
.stars{margin-top:4px;color:var(--orange);font-size:13px;letter-spacing:1px}
.result-card p{margin:10px 30px 0;font-size:12.5px;line-height:21px}

/* footer */
.footer-nav{left:0;top:2726px;width:1200px;height:46px;background:var(--band);display:flex;justify-content:center;align-items:center;font-size:12px;color:#333;gap:28px}
.news-title{left:0;top:2826px;width:1200px;text-align:center;color:var(--orange);font-family:"Jost",sans-serif;font-weight:500;font-size:21px}
.news-text{left:170px;top:2866px;width:860px;text-align:center;font-size:12.5px;line-height:25px}
.news-form{left:353px;top:2948px;width:492px;height:48px;border:1px solid #bbb;border-radius:24px;overflow:hidden;display:flex}
.news-form .field{flex:1;padding-left:26px;line-height:46px;font-size:14px;color:#888}
.news-form .submit{width:141px;background:linear-gradient(#5b9c2b,var(--green-dark));color:#fff;font-size:15px;font-weight:600;text-align:center;line-height:46px}
.social{left:0;top:3034px;width:1200px;display:flex;justify-content:center;gap:17px}
.social span{width:46px;height:46px;border-radius:50%}
.rule{left:0;top:3117px;width:1200px;height:1px;background:#ddd}
.copyright{left:0;top:3136px;width:1200px;text-align:center;font-size:12px;color:var(--muted)}
.page-code{left:1144px;top:3136px;font-size:12px;color:var(--muted)}
</style>
</head>
<body>

<!-- Hero -->
<section class="abs hero" role="img" aria-label="Photo of a fit man and woman holding dumbbells against a dark wall"></section>
<div class="abs brand"><span class="mark"></span>TRIMVALE FITNESS</div>
<nav class="abs nav">
  <span style="left:573px">Home</span>
  <span style="left:674px">About</span>
  <span style="left:769px">Recipe</span>
  <span style="left:864px">FAQ</span>
  <span style="left:929px">Blog</span>
  <span style="left:1017px">Contact Us</span>
</nav>
<svg class="abs nav-underline" width="70" height="12" viewBox="0 0 70 12"><path d="M4 3 Q35 14 66 3" stroke="#e8681c" stroke-width="3" fill="none" stroke-linecap="round"/></svg>
<svg class="abs arrow-side" style="left:28px" width="20" height="52" viewBox="0 0 20 52"><path d="M17 2 L3 26 L17 50" stroke="#ddd" stroke-width="2" fill="none"/></svg>
<svg class="abs arrow-side" style="left:1144px" width="20" height="52" viewBox="0 0 20 52"><path d="M3 2 L17 26 L3 50" stroke="#ddd" stroke-width="2" fill="none"/></svg>
<h1 class="abs hero-title">MODERN WEIGHT LOSS TECHNIQUES</h1>
<p class="abs hero-sub">MODERN WEIGHT LOSS TECHNIQUES PHYSICALLY AND MENTALLY FIT</p>
<div class="abs hero-btn">VIEW MORE INFORMATION</div>
<svg class="abs scroll-down" width="76" height="76" viewBox="0 0 76 76"><circle cx="38" cy="38" r="36" stroke="#fff" stroke-width="2" fill="none"/><path d="M24 32 L38 46 L52 32" stroke="#fff" stroke-width="2.5" fill="none"/></svg>

<!-- Welcome -->
<h2 class="abs heading" style="left:0;top:690px;width:1200px">WELCOME TO <span class="accent">TRIMVALE FITNESS</span></h2>
<div class="ornament" style="left:370px;top:753px;width:460px"><i></i></div>
<p class="abs intro">Lorem Ipsum is simply dummy text of the printing and typesetting industry. Lorem Ipsum has been the industry's standard dummy text ever since the 1500s, when an unknown printer took a galley of type and scrambled it to make a type specimen book.</p>

<div class="abs feature" style="left:132px">
  <div class="circle"><svg width="56" height="56" viewBox="0 0 56 56" fill="none" stroke="#fff" stroke-width="3"><path d="M14 14 H34 L31 46 H17 Z"/><circle cx="40" cy="38" r="8"/></svg></div>
  <h3>Diet</h3>
  <p>Lorem Ipsum is simply dummy text of the printing and typesetting industry. Lorem Ipsum industry's</p>
</div>
<div class="abs feature" style="left:473px">
  <div class="circle active"><svg width="60" height="40" viewBox="0 0 60 40" fill="#fff"><rect x="4" y="10" width="7" height="20"/><rect x="12" y="6" width="7" height="28"/><rect x="19" y="18" width="22" height="4"/><rect x="41" y="6" width="7" height="28"/><rect x="49" y="10" width="7" height="20"/></svg></div>
  <h3>Exercises</h3>
  <p>Lorem Ipsum is simply dummy text of the printing and typesetting industry. Lorem Ipsum industry's</p>
</div>
<div class="abs feature" style="left:815px">
  <div class="circle"><svg width="56" height="56" viewBox="0 0 56 56" fill="none" stroke="#fff" stroke-width="3"><circle cx="28" cy="28" r="18"/><circle cx="28" cy="28" r="6" fill="#fff"/></svg></div>
  <h3>Yoga</h3>
  <p>Lorem Ipsum is simply dummy text of the printing and typesetting industry. Lorem Ipsum industry's</p>
</div>

<!-- Weight loss techniques -->
<section class="abs techniques" role="img" aria-label="Dark background photo of people training in a gym"></section>
<h2 class="abs heading" style="left:0;top:1190px;width:1200px;color:#fff">WEIGHT LOSS TECHNIQUES</h2>
<div class="ornament" style="left:382px;top:1246px;width:438px;background:#fff"><i style="box-shadow:0 0 0 5px #2e2b28"></i></div>
<p class="abs tech-sub">Lorem ipsum dolor sit amet, consectetur adipiscing elit. Sed rhoncus ligula vel tincidunt</p>

<article class="abs tech-card" style="left:99px">
  <div class="photo" role="img" aria-label="Woman doing a squat with a kettlebell" style="background:linear-gradient(#d9d9d9,#8f8f8f)"></div>
  <h4>Finibus Bonorum et Malor</h4>
  <p>Sed ut perspiciatis unde omnist enatus error sit voluptatem accusa ntium doloremque laudan</p>
  <div class="btn-green">Read More</div>
</article>
<article class="abs tech-card" style="left:354px">
  <div class="photo" role="img" aria-label="Woman stretching at a ballet barre" style="background:linear-gradient(#f1f1f1,#bdbdbd)"></div>
  <h4>Finibus Bonorum et Malor</h4>
  <p>Sed ut perspiciatis unde omnist enatus error sit voluptatem accusa ntium doloremque laudan</p>
  <div class="btn-green">Read More</div>
</article>
<article class="abs tech-card" style="left:608px">
  <div class="photo" role="img" aria-label="Trainer helping a woman stretch on a mat" style="background:linear-gradient(#b98d6e,#4d3a30)"></div>
  <h4>Finibus Bonorum et Malor</h4>
  <p>Sed ut perspiciatis unde omnist enatus error sit voluptatem accusa ntium doloremque laudan</p>
  <div class="btn-green">Read More</div>
</article>
<article class="abs tech-card" style="left:864px">
  <div class="photo" role="img" aria-label="Woman measuring her waist with a tape" style="background:linear-gradient(#f3eee6,#d2c3ad)"></div>
  <h4>Finibus Bonorum et Malor</h4>
  <p>Sed ut perspiciatis unde omnist enatus error sit voluptatem accusa ntium doloremque laudan</p>
  <div class="btn-green">Read More</div>
</article>

<!-- Exercise -->
<div class="abs exercise-photo" role="img" aria-label="Fit woman with a water bottle and man lifting a dumbbell"></div>
<h2 class="abs heading exercise-title">EXERCISE OF FIT AND HEALTHY LIVING</h2>
<div class="ornament" style="left:545px;top:1828px;width:537px"><i></i></div>
<p class="abs exercise-text">It is a long established fact that a reader will be distracted by the readable content of a page when looking at its layout. The point of using Lorem Ipsum is that it has a more-or-less normal distribution of letters, as opposed to using 'Content here, content here', making it look like readable English. Many desktop publishing packages and web page editors now use Lorem Ipsum as their default model text, and a search for 'lorem ipsum' will uncover many web sites still in their infancy. Various versions have evolved over the years</p>
<div class="abs btn-green exercise-btn">Read More</div>

<!-- Before and after -->
<section class="abs results"></section>
<h2 class="abs heading" style="left:0;top:2168px;width:1200px">BEFORE AND AFTER</h2>
<div class="ornament" style="left:463px;top:2216px;width:274px;background:#333"><i style="box-shadow:0 0 0 5px var(--light)"></i></div>

<article class="abs result-card" style="left:99px">
  <div class="photo" role="img" aria-label="Woman before and after weight loss"><div style="background:linear-gradient(#f2f2f2,#d8cfc6)"></div><div style="background:linear-gradient(#f2f2f2,#cfc6bd)"></div>
    <div class="label"><span>Before</span><span>After</span></div></div>
  <h4>Marisol</h4>
  <div class="stars">★★★★★</div>
  <p>Hair on back of head is trimmed and a narrow strip is surgically removed so that hair can grow through and camouflage the scar.Hair on back of head is trimmed and a narrow strip is surgically</p>
</article>
<article class="abs result-card" style="left:445px">
  <div class="photo" role="img" aria-label="Man in red shirt before and after weight loss"><div style="background:linear-gradient(#f2f2f2,#d46a6a)"></div><div style="background:linear-gradient(#f2f2f2,#d67a7a)"></div>
    <div class="label"><span>Before</span><span>After</span></div></div>
  <h4>Owen Barrett</h4>
  <div class="stars">★★★★★</div>
  <p>Hair on back of head is trimmed and a narrow strip is surgically removed so that hair can grow through and camouflage the scar.Hair on back of head is trimmed and a narrow strip is surgically</p>
</article>
<article class="abs result-card" style="left:791px">
  <div class="photo" role="img" aria-label="Woman in white top before and after weight loss"><div style="background:linear-gradient(#f2f2f2,#c9c3d3)"></div><div style="background:linear-gradient(#f2f2f2,#cdc7d6)"></div>
    <div class="label"><span>Before</span><span>After</span></div></div>
  <h4>Delia</h4>
  <div class="stars">★★★★★</div>
  <p>Hair on back of head is trimmed and a narrow strip is surgically removed so that hair can grow through and camouflage the scar.Hair on back of head is trimmed and a narrow strip is surgically</p>
</article>

<!-- Footer -->
<nav class="abs footer-nav">
  <span>HOME</span><span>/</span><span>ABOUT</span><span>/</span><span>RECIPE</span><span>/</span><span>FAQ</span><span>/</span><span>BLOG</span><span>/</span><span>CONTACT US</span>
</nav>
<h3 class="abs news-title">NEWSLETTER SIGNUP</h3>
<p class="abs news-text">Lorem Ipsum is simply dummy text of the printing and typesetting industry. Lorem Ipsum has been the industry's standard dummy text ever since the 1500s, when an unknown printer took a galley of type and scrambled it to make a type specimen book.</p>
<div class="abs news-form"><div class="field">Enter your email address...</div><div class="submit">Submit</div></div>
<div class="abs social">
  <span style="background:#3b5ea8"></span>
  <span style="background:#2fa3dc"></span>
  <span style="background:#1f6fa5"></span>
  <span style="background:#f39a1d"></span>
  <span style="background:#d42a26"></span>
  <span style="background:#4a4a4a"></span>
  <span style="background:#d8232a"></span>
</div>
<div class="abs rule"></div>
<p class="abs copyright">© 2016, Trimvale Fitness.All Rights Reserved.</p>
<span class="abs page-code">C12</span>

</body>
</html>
```